Redesign current business card for food company

i would like to redesign my business card. our company is food company, our product range from chips, juices, milk and etc (mostly dried food stuff).
I want o keep same logo but , the rest is open to new design.
you can check at our website about our company www.orvelpantry.com

Target Market(s)

most of food company

Industry/Entity Type

Business

Contact Information for Business Card

I want to keep more to blue color...

Colors
3176b5
abd036

Requirements
Must have
• our old logo
Nice to have
• we do not mind to have nice material on bus card in order to accomplish nice design. for example: using spot uv, embossed and etc.

```html
<!DOCTYPE html>
<html lang="en">
<head>
<meta charset="utf-8">
<title>Orvel Pantry – Business Card</title>
<link rel="stylesheet" href="https://fonts.googleapis.com/css2?family=Source+Sans+3:wght@400;600&display=swap">
<style>
  :root {
    --backdrop: #4a423d;
    --card: #1c1c1d;
    --card-edge: #2a2a2b;
    --silver: #c9cbcd;
    --brand-blue: #3176b5;
    --name-blue: #2f6fd8;
    --brand-green: #abd036;
    --title-green: #3fb33f;
    --text-light: #e6e6e6;
    --divider: #5a5a5c;
  }
  html, body {
    margin: 0;
    width: 1200px;
    height: 814px;
    overflow: hidden;
    background: var(--backdrop);
    font-family: "Source Sans 3", sans-serif;
  }
  .stage {
    position: relative;
    width: 1200px;
    height: 814px;
  }
  .card {
    position: absolute;
    top: 264px;
    width: 500px;
    height: 286px;
    background: var(--card);
    border: 1px solid var(--card-edge);
    box-sizing: border-box;
    box-shadow: 0 10px 24px rgba(0,0,0,0.45);
  }
  .card--front { left: 70px; }
  .card--back { left: 630px; }

  .wordmark {
    font-weight: 400;
    letter-spacing: 1px;
    line-height: 1;
  }
  .card--front .wordmark {
    position: absolute;
    left: 0; right: 0;
    top: 100px;
    text-align: center;
    font-size: 84px;
    color: var(--silver);
  }
  .card--back .wordmark {
    position: absolute;
    left: 28px;
    top: 104px;
    font-size: 62px;
    color: var(--brand-blue);
  }
  .divider {
    position: absolute;
    left: 236px;
    top: 40px;
    width: 1px;
    height: 206px;
    background: linear-gradient(to bottom, transparent, var(--divider) 20%, var(--divider) 80%, transparent);
  }
  .details {
    position: absolute;
    left: 256px;
    top: 42px;
    color: var(--text-light);
    font-size: 15px;
    line-height: 19px;
  }
  .details .person-name {
    color: var(--name-blue);
    font-size: 19px;
    font-weight: 600;
    line-height: 22px;
  }
  .details .person-title {
    color: var(--title-green);
    font-size: 14px;
    font-weight: 600;
    margin-bottom: 8px;
  }
  .details .address { margin-bottom: 2px; }
  .contact-row {
    display: flex;
    align-items: center;
    gap: 7px;
  }
  .contact-row svg {
    width: 12px;
    height: 12px;
    flex: none;
    fill: var(--name-blue);
  }
</style>
</head>
<body>
<div class="stage">
  <div class="card card--front">
    <div class="wordmark">orvel</div>
  </div>

  <div class="card card--back">
    <div class="wordmark">orvel</div>
    <div class="divider"></div>
    <div class="details">
      <div class="person-name">Daniel Hartono</div>
      <div class="person-title">President</div>
      <div class="address">2840 Linden Ave.<br>Corona CA 92880</div>
      <div class="contact-row">
        <svg viewBox="0 0 12 12" aria-hidden="true"><path d="M2.5 1 L4.5 1 L5.3 3.5 L4 4.6 Q5 7 7.4 8 L8.5 6.7 L11 7.5 L11 9.5 Q10.5 11 9 11 Q1 10 1 2.5 Q1 1 2.5 1 Z"/></svg>
        <span>951 402 3175</span>
      </div>
      <div class="contact-row">
        <svg viewBox="0 0 12 12" aria-hidden="true"><path d="M3.5 0.5 H8.5 A1 1 0 0 1 9.5 1.5 V10.5 A1 1 0 0 1 8.5 11.5 H3.5 A1 1 0 0 1 2.5 10.5 V1.5 A1 1 0 0 1 3.5 0.5 Z M3.6 2 V9 H8.4 V2 Z"/></svg>
        <span>951 718 2046</span>
      </div>
      <div class="contact-row">
        <svg viewBox="0 0 12 12" aria-hidden="true"><path d="M3 1 H9 V4 H11 V10 H1 V4 H3 Z M4 2 V4 H8 V2 Z M3 6 V7 H5 V6 Z M6.5 6 V7 H9 V6 Z"/></svg>
        <span>951 402 3190</span>
      </div>
      <div class="contact-row">
        <svg viewBox="0 0 12 12" aria-hidden="true"><path d="M1 2.5 H11 V9.5 H1 Z M1.8 3.2 L6 6.4 L10.2 3.2 Z"/></svg>
        <span>Daniel@orvelpantry.com</span>
      </div>
      <div class="contact-row">
        <svg viewBox="0 0 12 12" aria-hidden="true"><circle cx="6" cy="6" r="5.5"/></svg>
        <span>www.orvelpantry.com</span>
      </div>
    </div>
  </div>
</div>
</body>
</html>
```